Coffee and Plastics

I am looking for a completely new site that shows the products we have. Our current site is www.velmorebrothersbeans.com. We are open minded to what designers come up with. Our current site is www.velmorebrothersbeans.com. You can you the information from there to start the site. I need these tabs on the main home page. ( Home, Coffee & Tea, Condiments, and Paper and Plastics, and Contact.) You can take photos and info from my Current site. In products page.
I will be uploading info and photo for paper and plastics.
Look and feel
Each slider illustrates characteristics of the customer's brand and the style your logo design should communicate.

```html
<!DOCTYPE html>
<html lang="en">
<head>
<meta charset="utf-8">
<title>Velmore Brothers Beans</title>
<link href="https://fonts.googleapis.com/css2?family=Ubuntu:wght@400;500;700&family=Questrial&family=Arimo:wght@400;700&family=Signika:wght@600;700&display=swap" rel="stylesheet">
<style>
:root{
  --page:#e6d5c0;
  --panel:#d9c3aa;
  --nav:#7a2a06;
  --nav-line:#63200a;
  --band:#8a2e08;
  --footer:#913008;
  --cream:#fbf4e8;
  --gold:#f0c54a;
  --rust:#8a2e08;
  --ink:#1c120c;
  --body:#4a3a2e;
}
*{margin:0;padding:0;box-sizing:border-box}
html,body{width:1200px;height:1189px;overflow:hidden;background:var(--page)}
.site{position:relative;width:1200px;height:1189px;font-family:"Arimo",Arial,sans-serif}

.hero{position:absolute;left:0;top:0;width:1200px;height:740px;
  background:linear-gradient(to bottom,#5e3a22 0%,#9a7150 14%,#b48c68 40%,#c4a180 70%,#d8c2a6 88%,var(--page) 100%);}

.nav{position:absolute;left:0;top:99px;width:1200px;height:56px;background:var(--nav);
  box-shadow:0 2px 6px rgba(0,0,0,.35)}
.nav a{position:absolute;top:0;height:56px;line-height:56px;color:var(--cream);
  font-family:"Ubuntu",sans-serif;font-size:15px;text-decoration:none}
.nav .divider{position:absolute;top:0;width:1px;height:56px;background:var(--nav-line)}

.brand{position:absolute;left:537px;top:25px;width:182px;height:182px;border-radius:50%;
  background:var(--nav);border:3px solid var(--gold);box-shadow:0 4px 10px rgba(0,0,0,.4);
  display:flex;align-items:center;justify-content:center;text-align:center;
  font-family:"Signika",sans-serif;font-weight:700;font-size:24px;line-height:1.25;color:var(--cream)}

.hero-title{position:absolute;left:500px;top:343px;width:530px;text-align:center;
  font-family:"Questrial",sans-serif;font-size:56px;color:#eadfcf;letter-spacing:.5px}
.hero-sub{position:absolute;left:500px;top:420px;width:530px;text-align:center;
  font-family:"Signika",sans-serif;font-weight:700;font-size:58px;color:var(--gold)}

.slide-arrow{position:absolute;top:386px;width:44px;height:44px;border-radius:50%;background:#5a2e18}
.slide-arrow svg{position:absolute;left:7px;top:7px}

.welcome{position:absolute;left:181px;top:726px;width:839px;height:275px;background:var(--panel)}
.welcome-photo{position:absolute;left:19px;top:22px;width:237px;height:230px;
  background:radial-gradient(ellipse at 55% 55%,#8a4d22 0%,#4a2a14 55%,#1a0f08 100%)}
.welcome-text{position:absolute;left:285px;top:20px;width:535px}
.welcome-text h1{font-family:"Questrial",sans-serif;font-weight:400;font-size:22px;color:var(--ink);margin-bottom:9px}
.welcome-text h1 span{color:var(--rust)}
.welcome-text p{font-size:11px;line-height:20.5px;color:var(--body);text-align:justify;margin-bottom:15px}

.partners{position:absolute;left:0;top:1047px;width:1200px;height:76px;background:var(--band)}
.partners .arrow{position:absolute;top:24px}
.badge{position:absolute;top:19px;width:68px;height:38px;border-radius:6px;background:#c9b8a4;border:2px solid #f1e6d8}

.footer{position:absolute;left:0;top:1123px;width:1200px;height:66px;background:var(--footer);color:var(--cream)}
.copyright{position:absolute;left:181px;top:26px;font-size:11.5px}
.social{position:absolute;top:20px;width:27px;height:27px;border-radius:50%;border:2px solid var(--cream)}
.footer-links{position:absolute;right:180px;top:27px;font-size:11.5px}
.footer-links a{color:var(--cream);text-decoration:none}
.footer-links .sep{margin:0 8px}
</style>
</head>
<body>
<div class="site">
  <div class="hero" role="img" aria-label="Steaming white coffee cup on a saucer with roasted coffee beans scattered on burlap"></div>

  <nav class="nav">
    <a href="#" style="left:180px">Home</a>
    <span class="divider" style="left:256px"></span>
    <a href="#" style="left:285px">Coffee &amp; Tea</a>
    <span class="divider" style="left:404px"></span>
    <a href="#" style="left:429px">Condiments</a>
    <a href="#" style="left:757px">Paper</a>
    <span class="divider" style="left:832px"></span>
    <a href="#" style="left:859px">Plastics</a>
    <span class="divider" style="left:942px"></span>
    <a href="#" style="left:970px">Contact</a>
  </nav>

  <div class="brand">Velmore<br>Brothers</div>

  <div class="hero-title">Velmore Brothers</div>
  <div class="hero-sub">Coffee</div>

  <div class="slide-arrow" style="left:54px">
    <svg width="30" height="30" viewBox="0 0 30 30"><circle cx="15" cy="15" r="14" fill="#f4f0ea"/><path d="M17 9l-6 6 6 6" fill="none" stroke="#6a5a4e" stroke-width="2.5" stroke-linecap="round"/></svg>
  </div>
  <div class="slide-arrow" style="left:1100px">
    <svg width="30" height="30" viewBox="0 0 30 30"><circle cx="15" cy="15" r="14" fill="#f4f0ea"/><path d="M13 9l6 6-6 6" fill="none" stroke="#6a5a4e" stroke-width="2.5" stroke-linecap="round"/></svg>
  </div>

  <section class="welcome">
    <div class="welcome-photo" role="img" aria-label="Burlap sack of roasted coffee beans with metal scoops"></div>
    <div class="welcome-text">
      <h1>Welcome to <span>Velmore Brothers Beans</span></h1>
      <p>We are a family-owned and operated business based in Marlow Texas. Since the opening of the Velmore Brothers plant in 1995, we have become Texas' premier independently owned coffee packaging company. Our success relies solely on the principle of selling only the freshest, highest-quality in-room coffee available.</p>
      <p>Velmore Brothers packages and supplies in-room coffee, tea products, and condiments. Whether we're supplying a 50-room Hotel or a 500-room grand resort, we have the distribution capacity to fill your rooms with the most aromatic and robust coffees and teas available at competitive prices.</p>
      <p>Velmore Brothers is continuously striving for ways to improve quality and product appearance to meet the highest standards in today's franchises and independent hotels.</p>
    </div>
  </section>

  <section class="partners">
    <svg class="arrow" style="left:181px" width="28" height="28" viewBox="0 0 28 28"><circle cx="14" cy="14" r="12.5" fill="none" stroke="#fbf4e8" stroke-width="2"/><path d="M20 14H8M13 9l-5 5 5 5" fill="none" stroke="#fbf4e8" stroke-width="2" stroke-linecap="round" stroke-linejoin="round"/></svg>
    <div class="badge" style="left:239px"></div>
    <div class="badge" style="left:335px"></div>
    <div class="badge" style="left:427px"></div>
    <div class="badge" style="left:522px"></div>
    <div class="badge" style="left:622px"></div>
    <div class="badge" style="left:712px"></div>
    <div class="badge" style="left:802px"></div>
    <div class="badge" style="left:895px"></div>
    <svg class="arrow" style="left:990px" width="28" height="28" viewBox="0 0 28 28"><circle cx="14" cy="14" r="12.5" fill="none" stroke="#fbf4e8" stroke-width="2"/><path d="M8 14h12M15 9l5 5-5 5" fill="none" stroke="#fbf4e8" stroke-width="2" stroke-linecap="round" stroke-linejoin="round"/></svg>
  </section>

  <footer class="footer">
    <div class="copyright">©2014 2014&nbsp; Velmore Brothers Beans, All Rights Reserved.</div>
    <span class="social" style="left:558px"></span>
    <span class="social" style="left:592px"></span>
    <span class="social" style="left:626px"></span>
    <div class="footer-links">
      <a href="#">Home</a><span class="sep">|</span>
      <a href="#">Coffee &amp; Tea</a><span class="sep">|</span>
      <a href="#">Condiments</a><span class="sep">|</span>
      <a href="#">Paper</a><span class="sep">|</span>
      <a href="#">Contact</a>
    </div>
  </footer>
</div>
</body>
</html>
```